van wrap for house/commercial painting company

We are rebranding and i need a new design for a los angeles based painting company.  New business name will be Orla Painting and the vehicle is a bex cargolux 2300.
We offer our services to houses, hoa's, commercial and specializing in interior/exterior, wood staining, cabinet refinishing, drywall repair.
We would love a colorful but easy to read design to grab attention when at job sites or on the road.
I attached our current wrap which we no longer like and looking for a different look/feel. I attached our current logo but the color splash is not necessary if  design flows better without it.

house painting
- easy to read phone number and contact info

```html
<!DOCTYPE html>
<html lang="en">
<head>
<meta charset="utf-8">
<title>Orla Painting – Van Wrap Panels</title>
<link rel="stylesheet" href="https://fonts.googleapis.com/css2?family=Montserrat:wght@600;800&family=Roboto:wght@500;700&family=Oswald:wght@500&display=swap">
<style>
  :root {
    --teal-deep: #1f8f8c;
    --teal-mid: #2ab3b0;
    --teal-bright: #3fd6d6;
    --ink: #333638;
    --paper: #ffffff;
    --backdrop: #ffffff;
  }
  html, body {
    margin: 0;
    padding: 0;
    width: 1119px;
    height: 1200px;
    overflow: hidden;
    background: var(--backdrop);
  }
  .wrap-sheet { display: block; width: 1119px; height: 1200px; }
  .brand-word { font-family: "Montserrat", sans-serif; font-weight: 800; }
  .brand-sub { font-family: "Montserrat", sans-serif; font-weight: 600; letter-spacing: 0.32em; }
  .body-text { font-family: "Roboto", sans-serif; font-weight: 700; }
  .social-text { font-family: "Roboto", sans-serif; font-weight: 700; }
  .service-list { font-family: "Oswald", sans-serif; font-weight: 500; letter-spacing: 0.04em; }
  .ink { fill: var(--ink); }
  .teal { fill: var(--teal-deep); }
  .white { fill: var(--paper); }
</style>
</head>
<body>
<svg class="wrap-sheet" viewBox="0 0 1119 1200" xmlns="http://www.w3.org/2000/svg">
  <defs>
    <linearGradient id="tealFacet" x1="0" y1="0" x2="1" y2="1">
      <stop offset="0" stop-color="#2fc7c6"/>
      <stop offset="0.45" stop-color="#1f9693"/>
      <stop offset="0.75" stop-color="#35cfcf"/>
      <stop offset="1" stop-color="#1c8a88"/>
    </linearGradient>
  </defs>

  <!-- SIDE PANEL -->
  <g class="side-panel">
    <rect class="side-base" x="70" y="60" width="950" height="360" rx="30" fill="var(--paper)" stroke="#d9dddd" stroke-width="1.5"/>
    <path class="side-facet-band" role="img" aria-label="Teal faceted geometric pattern"
          d="M70 275 L1020 268 L1020 390 Q1020 420 990 420 L100 420 Q70 420 70 390 Z" fill="url(#tealFacet)"/>
    <path class="side-facet-wedge" role="img" aria-label="Teal faceted geometric pattern"
          d="M715 60 L990 60 Q1020 60 1020 90 L1020 268 L800 270 Z" fill="url(#tealFacet)"/>

    <text class="body-text ink" x="603" y="78" font-size="12.5" text-anchor="middle">COMMERCIAL AND RESIDENTIAL</text>
    <text class="body-text ink" x="603" y="90" font-size="12.5" text-anchor="middle">SPECIALIZING</text>

    <text class="brand-word ink" x="497" y="177" font-size="94" textLength="228" lengthAdjust="spacingAndGlyphs">ORLA</text>
    <text class="brand-sub ink" x="510" y="212" font-size="28">PAINTING</text>
    <text class="body-text teal" x="516" y="258" font-size="31">555.014.2287</text>

    <text class="body-text ink" x="363" y="253" font-size="15" text-anchor="middle">Fully Licensed</text>
    <text class="body-text ink" x="363" y="267" font-size="15" text-anchor="middle">Bonded &amp; Insured</text>

    <g class="social-row">
      <text class="social-text white" x="878" y="232" font-size="15">Ratewell</text>
      <circle cx="947" cy="227" r="6" fill="var(--paper)"/>
    </g>
    <text class="body-text white" x="914" y="251" font-size="11" text-anchor="middle">JHON 1:12-13</text>
    <text class="body-text white" x="914" y="265" font-size="11" text-anchor="middle">LICENSE # 047319</text>
    <text class="body-text white" x="900" y="288" font-size="18" text-anchor="middle">orlapainting.com</text>

    <text class="body-text white" x="558" y="312" font-size="14.5" text-anchor="middle">EXTERIOR - INTERIOR - WOOD STAINING</text>
    <text class="body-text white" x="558" y="331" font-size="14.5" text-anchor="middle">CABINET REFINISHING - DRYWALL REPAIR &amp; MORE</text>
  </g>

  <!-- REAR PANEL -->
  <g class="rear-panel">
    <rect class="rear-facet" role="img" aria-label="Teal faceted geometric pattern"
          x="62" y="605" width="420" height="470" rx="26" fill="url(#tealFacet)"/>
    <line x1="266" y1="605" x2="266" y2="1075" stroke="#176f6d" stroke-width="2"/>

    <text class="body-text white" x="258" y="653" font-size="19" text-anchor="middle">Commercial &amp; Residential</text>
    <text class="body-text white" x="258" y="673" font-size="19" text-anchor="middle">Specializing</text>

    <text class="brand-word white" x="258" y="778" font-size="84" text-anchor="middle">ORLA</text>
    <text class="brand-sub white" x="258" y="808" font-size="23" text-anchor="middle">PAINTING</text>

    <text class="body-text white" x="177" y="870" font-size="22" text-anchor="middle">555.014.2287</text>
    <text class="body-text white" x="177" y="895" font-size="18" text-anchor="middle">orlapainting.com</text>

    <g class="social-row">
      <text class="social-text white" x="342" y="865" font-size="13">Ratewell</text>
      <circle cx="405" cy="861" r="5.5" fill="var(--paper)"/>
    </g>
    <text class="body-text white" x="379" y="882" font-size="10.5" text-anchor="middle">JHON 1:12-13</text>
    <text class="body-text white" x="379" y="895" font-size="10.5" text-anchor="middle">LICENSE # 047319</text>

    <g class="service-list white" font-size="11.5">
      <path d="M278 910 l9 5 -9 5 z M278 927 l9 5 -9 5 z M278 944 l9 5 -9 5 z M278 961 l9 5 -9 5 z M278 978 l9 5 -9 5 z" fill="none" stroke="var(--paper)" stroke-width="1.4"/>
      <text x="294" y="920">EXTERIOR</text>
      <text x="294" y="937">INTERIOR</text>
      <text x="294" y="954">WOOD STAINING</text>
      <text x="294" y="971">CABINET REFINISHING</text>
      <text x="294" y="988">DRYWALL REPAIR &amp; MORE</text>
    </g>
  </g>

  <!-- FRONT HOOD PANEL -->
  <g class="hood-panel">
    <rect class="hood-base" x="585" y="770" width="470" height="150" rx="24" fill="var(--paper)" stroke="#d9dddd" stroke-width="1.5"/>
    <path class="hood-facet-band" role="img" aria-label="Teal faceted geometric pattern"
          d="M663 797 L977 797 L940 905 L708 905 Z" fill="url(#tealFacet)"/>
    <text class="brand-word white" x="820" y="866" font-size="46" text-anchor="middle">ORLA</text>
    <text class="brand-sub white" x="820" y="884" font-size="13" text-anchor="middle">PAINTING</text>
  </g>
</svg>
</body>
</html>
```